Valderons Business Card

Business card for philanthropic organization

Industry/Entity Type

Business

Contact Information for Business Card

Need a very ELEGANT, sober, embossed, formal business card... it should transmit CREDIBILITY. Not looking for a "fun card". would like white, grays or black designs.

Font styles to use
Script

Requirements
Must have
• Embossed look

```html
<!DOCTYPE html>
<html lang="en">
<head>
<meta charset="utf-8">
<title>Valderons Business Card</title>
<link href="https://fonts.googleapis.com/css2?family=PT+Sans:wght@400;700&display=swap" rel="stylesheet">
<style>
  :root {
    --backdrop: #a6a6a6;
    --card: #f7f7f5;
    --gold: #c08a3e;
    --gold-dark: #8a5e22;
    --ink: #3a3a3a;
    --emboss-light: rgba(255,255,255,0.9);
    --emboss-dark: rgba(0,0,0,0.28);
  }
  * { margin: 0; padding: 0; box-sizing: border-box; }
  html, body { width: 1200px; height: 881px; overflow: hidden; }
  body {
    background: var(--backdrop);
    display: flex; align-items: center; justify-content: center;
    font-family: "PT Sans", sans-serif;
  }
  .business-card {
    position: relative;
    width: 1000px; height: 571px;
    background: var(--card);
    box-shadow: 0 18px 40px rgba(0,0,0,0.25);
  }
  .identity {
    position: absolute; left: 70px; top: 120px;
    color: var(--gold);
    font-weight: 700; font-size: 30px; line-height: 1.08;
    letter-spacing: 0.5px; text-transform: uppercase;
    text-shadow: -1px -1px 0 var(--emboss-light), 1px 1px 1px var(--emboss-dark);
  }
  .contact-list {
    position: absolute; left: 70px; top: 236px;
    list-style: none;
    color: var(--ink); font-size: 25px; line-height: 1.2;
    text-shadow: -1px -1px 0 var(--emboss-light), 1px 1px 1px var(--emboss-dark);
  }
  .contact-list li { display: flex; align-items: center; gap: 14px; }
  .contact-icon { width: 20px; height: 20px; flex: none; }
  .brand-name {
    position: absolute; right: 110px; top: 175px;
    display: flex; align-items: center; gap: 12px;
    color: var(--gold); font-weight: 700; font-size: 34px;
  }
  .brand-mark { width: 22px; height: 22px; border-radius: 50%; background: var(--gold); }
  .mail-address {
    position: absolute; right: 70px; bottom: 70px;
    text-align: right; color: var(--ink);
    font-size: 25px; line-height: 1.15;
    text-shadow: -1px -1px 0 var(--emboss-light), 1px 1px 1px var(--emboss-dark);
  }
</style>
</head>
<body>
  <article class="business-card">
    <header class="identity">
      <div>Mateo Villareal</div>
      <div>Noor Halim Valderons</div>
      <div>Potentate 2017</div>
    </header>

    <ul class="contact-list">
      <li>
        <svg class="contact-icon" viewBox="0 0 20 20" aria-hidden="true">
          <circle cx="10" cy="10" r="10" fill="var(--gold)"/>
          <path d="M6 5 L8 5 L9 8 L8 9 Q9 11 11 12 L12 11 L15 12 L15 14 Q10 15 6 9 Z" fill="#fff"/>
        </svg>
        +(507)-6000-1234
      </li>
      <li>
        <svg class="contact-icon" viewBox="0 0 20 20" aria-hidden="true">
          <circle cx="10" cy="10" r="10" fill="var(--gold)"/>
          <rect x="5" y="6.5" width="10" height="7" fill="#fff"/>
          <path d="M5 6.5 L10 10.5 L15 6.5" fill="none" stroke="var(--gold)" stroke-width="1"/>
        </svg>
        mateovillareal@mail.com
      </li>
      <li>
        <svg class="contact-icon" viewBox="0 0 20 20" aria-hidden="true">
          <circle cx="10" cy="10" r="10" fill="var(--gold)"/>
          <circle cx="10" cy="10" r="5" fill="none" stroke="#fff" stroke-width="1.3"/>
          <path d="M5 10 H15 M10 5 Q7 10 10 15 M10 5 Q13 10 10 15" fill="none" stroke="#fff" stroke-width="1"/>
        </svg>
        www.mateovillareal.com
      </li>
    </ul>

    <div class="brand-name"><span class="brand-mark"></span>Valderons</div>

    <address class="mail-address" style="font-style:normal">
      <div>P.O. Box 0000-01234</div>
      <div>Panama, Republic of Panama</div>
    </address>
  </article>
</body>
</html>
```